2026 Varlo Kestin LWB Vehicle Wrap Design for Tallwood Electrical and Refrigeration Work Vans

We are Tallwood Electrical and Refrigeration — a Perth-based commercial electrical, air conditioning and refrigeration company. We service commercial buildings, homes and luxury residential jobs across the metro area and remote WA.
We need a clean, professional and high-impact full vehicle wrap design for our work vans. The vans are our mobile billboards, so the design needs to look sharp from a distance, communicate trust and competence, and clearly show what we do.
Must include:

Our company name: Tallwood Electrical and Refrigeration
Tagline options (you can choose the strongest placement or suggest alternatives):
“Electrical | Air Conditioning | Refrigeration – Perth & Remote WA”
Licence numbers "AU531207 and EC42918"
Phone number: 0412 555 318
Website: tallwoodelectricalrefrigeration.com.au
Email: admin@tallwoodelectricalrefrigeration.com.au
Our existing logo (will be uploaded)

Style we want:

Professional, modern and trustworthy
Bold enough to stand out on the road but not flashy or overly busy
Clean hierarchy so the company name and phone number are readable at speed
Strong use of contrast

Colour preferences:

Prefer designs that work with our existing branding (we will upload the logo and brand colours)
Open to strong, professional colour combinations (navy/dark blue, black, white, and one accent colour such as orange, red or electric blue often work well in the trades)

Avoid:

Cluttered designs with too much text
Cartoonish or overly “tradie” looking graphics
Designs that look cheap or dated

Additional notes:

Design should scale well so we can use the same concept across multiple vans
We will need print-ready files (high-res, layered) at the end

Please upload your best concepts. We will give clear feedback and work with the winning designer to refine the final artwork for production.

Target Market(s)

commercial buildings, homes and luxury residential jobs across the metro area and remote WA.

Industry/Entity Type

Electrical, Air Conditioning and Refrigeration

Colors
0054AA
0677BA
7BADD7
CADEEF
E8F1F8

Requirements
Must have
• Our company name: Tallwood Electrical and Refrigeration Tagline options (you can choose the strongest placement or suggest alternatives): “Electrical | Air Conditioning | Refrigeration – Perth & Remote WA” Licence numbers "AU531207 and EC42918" Phone number: 0412 555 318 Website: tallwoodelectricalrefrigeration.com.au Email: admin@tallwoodelectricalrefrigeration.com.au Our existing logo (will be uploaded)
Nice to have
• Professional, modern and trustworthy Bold enough to stand out on the road but not flashy or overly busy Clean hierarchy so the company name and phone number are readable at speed Strong use of contrast
Should not have
• Cluttered designs with too much text Cartoonish or overly “tradie” looking graphics Designs that look cheap or dated

```html
<!DOCTYPE html>
<html lang="en">
<head>
<meta charset="utf-8">
<title>Tallwood Electrical and Refrigeration — Van Wrap</title>
<link href="https://fonts.googleapis.com/css2?family=Poppins:wght@400;500;600;700&display=swap" rel="stylesheet">
<style>
  :root {
    --brand-blue: #0a63c9;
    --brand-blue-light: #2a7fdc;
    --wrap-grey: #8b8c8c;
    --body-white: #f4f4f2;
    --body-line: #d4d4d0;
    --panel-line: #dedede;
    --trim-dark: #2c2d2f;
    --trim-mid: #45474a;
    --glass: #5d6063;
    --glass-light: #8a8d90;
    --tyre: #1e1f21;
    --rim: #c9cacc;
    --rim-dark: #9c9ea1;
    --lamp-red: #b3202a;
    --lamp-clear: #e6e7e9;
    --shadow: #e9e9e9;
    --page-bg: #ffffff;
    --text-white: #ffffff;
  }
  html, body {
    margin: 0;
    padding: 0;
    width: 1200px;
    height: 1076px;
    overflow: hidden;
    background: var(--page-bg);
  }
  .wrap-sheet { display: block; width: 1200px; height: 1076px; }
  .wrap-sheet text { font-family: "Poppins", sans-serif; }

  .van-body { fill: var(--body-white); stroke: var(--body-line); stroke-width: 3; }
  .panel-line { fill: none; stroke: var(--panel-line); stroke-width: 3; }
  .van-trim { fill: var(--trim-dark); }
  .van-trim-mid { fill: var(--trim-mid); }
  .van-glass { fill: var(--glass); }
  .van-glass-light { fill: var(--glass-light); }
  .lamp-red { fill: var(--lamp-red); }
  .lamp-clear { fill: var(--lamp-clear); stroke: var(--rim-dark); stroke-width: 2; }
  .ground-shadow { fill: var(--shadow); }
  .tyre { fill: var(--tyre); }
  .rim { fill: var(--rim); stroke: var(--rim-dark); stroke-width: 4; }
  .hub { fill: var(--rim-dark); }
  .wheel-well { fill: var(--trim-dark); }

  .band-blue { fill: var(--brand-blue); }
  .band-blue-soft { fill: var(--brand-blue-light); opacity: .55; }
  .band-grey { fill: var(--wrap-grey); }
  .arch-swoosh { fill: none; stroke: var(--brand-blue); stroke-width: 40; }
  .brand-square { fill: var(--brand-blue); }

  .services { fill: var(--text-white); font-size: 14px; font-weight: 500; letter-spacing: .3px; }
  .region { fill: var(--text-white); font-size: 14px; font-weight: 700; }
  .divider { stroke: var(--text-white); stroke-width: 1.5; }
  .phone { fill: var(--text-white); font-size: 41px; font-weight: 700; }
  .brand-name { fill: var(--brand-blue); font-weight: 700; }
  .licence { fill: var(--trim-dark); font-size: 8px; font-weight: 600; }
  .website { fill: var(--text-white); font-size: 14px; font-weight: 500; letter-spacing: 1.4px; }
  .email { fill: var(--text-white); font-size: 11px; font-weight: 500; letter-spacing: .4px; }
</style>
</head>
<body>
<svg class="wrap-sheet" viewBox="0 0 2048 1836" xmlns="http://www.w3.org/2000/svg" aria-label="Tallwood Electrical and Refrigeration van wrap, side, rear and front views">

  <!-- Side view -->
  <g class="side-view">
    <ellipse class="ground-shadow" cx="1025" cy="790" rx="690" ry="18"/>
    <path class="van-body" d="M370 293 Q380 288 400 288 L1085 285 Q1190 287 1260 300 Q1330 320 1400 380 L1530 455 Q1640 500 1690 540 Q1712 560 1712 600 L1712 722 Q1705 742 1690 745 L345 745 Q336 740 336 720 L336 330 Q340 300 370 293 Z"/>

    <polygon class="band-grey" points="435,289 517,289 470,430"/>
    <polygon class="band-blue" points="517,289 845,285 735,600 735,745 500,745 385,665"/>
    <polygon class="band-blue-soft" points="560,289 600,289 470,665 430,665"/>
    <polygon class="band-blue-soft" points="640,289 660,289 540,640 520,640"/>
    <polygon class="band-grey" points="735,560 880,745 735,745"/>
    <path class="arch-swoosh" d="M1348 752 L1348 690 Q1365 600 1470 582 Q1565 572 1612 612"/>

    <path class="panel-line" d="M737 293 L737 742 M1078 290 L1078 742 M1095 300 L1095 715 Q1100 735 1150 738 L1330 738"/>
    <path class="panel-line" d="M1095 300 L1300 300 L1400 380 L1400 560"/>
    <path class="panel-line" d="M408 497 L735 497"/>

    <path class="van-glass" d="M1113 318 L1290 322 Q1350 345 1395 395 L1395 478 L1128 455 Z"/>
    <path class="van-glass-light" d="M1300 335 Q1340 360 1370 395 L1370 460 L1330 455 Z"/>
    <path class="van-glass" d="M1402 410 L1490 505 L1402 505 Z"/>
    <rect class="van-trim" x="1105" y="488" width="68" height="12" rx="6"/>
    <rect class="van-trim" x="1020" y="478" width="18" height="36" rx="6"/>

    <rect class="lamp-red" x="336" y="435" width="36" height="175" rx="6"/>
    <rect class="lamp-clear" x="340" y="525" width="14" height="55" rx="3"/>
    <path class="van-trim" d="M336 665 L520 665 L520 740 L350 740 Q336 738 336 725 Z"/>
    <path class="van-trim" d="M1600 580 L1705 585 L1712 720 L1690 745 L1620 745 L1600 700 Z"/>
    <path class="lamp-clear" d="M1562 488 Q1640 505 1695 545 L1690 558 Q1620 548 1580 548 Z"/>
    <rect class="van-trim-mid" x="1660" y="610" width="24" height="85" rx="4"/>
    <line x1="1190" y1="258" x2="1245" y2="295" stroke="#2c2d2f" stroke-width="4"/>

    <circle class="wheel-well" cx="612" cy="715" r="108"/>
    <circle class="wheel-well" cx="1488" cy="715" r="108"/>
    <g class="wheel">
      <circle class="tyre" cx="612" cy="715" r="94"/>
      <circle class="rim" cx="612" cy="715" r="62"/>
      <circle class="hub" cx="612" cy="715" r="14"/>
    </g>
    <g class="wheel">
      <circle class="tyre" cx="1488" cy="715" r="94"/>
      <circle class="rim" cx="1488" cy="715" r="62"/>
      <circle class="hub" cx="1488" cy="715" r="14"/>
    </g>

    <text class="services" x="602" y="362" text-anchor="middle">- ELECTRICAL -</text>
    <text class="services" x="602" y="382" text-anchor="middle">- AIR CONDITIONING -</text>
    <text class="services" x="602" y="401" text-anchor="middle">- REFRIGERATION -</text>
    <line class="divider" x1="586" y1="414" x2="618" y2="414"/>
    <text class="region" x="601" y="438" text-anchor="middle">Perth &amp; Remote WA</text>
    <text class="phone" x="590" y="567" text-anchor="middle">0412 555 318</text>

    <rect class="brand-square" x="832" y="415" width="174" height="166"/>
    <text class="brand-name" x="830" y="604" font-size="21">ELECTRICAL &amp;</text>
    <text class="brand-name" x="830" y="624" font-size="21">REFRIGERATION</text>
    <text class="brand-name" x="1012" y="430" font-size="14">TALLWOOD</text>

    <text class="licence" x="1440" y="533">Licence Nos:</text>
    <text class="licence" x="1440" y="544">AU531207 &amp; EC42918</text>
  </g>

  <!-- Rear view -->
  <g class="rear-view">
    <ellipse class="ground-shadow" cx="565" cy="1590" rx="330" ry="14"/>
    <rect class="tyre" x="300" y="1500" width="70" height="88" rx="14"/>
    <rect class="tyre" x="762" y="1500" width="70" height="88" rx="14"/>
    <path class="van-body" d="M318 1048 Q326 1040 345 1040 L800 1040 Q822 1040 830 1052 L852 1470 L280 1470 Z"/>
    <rect class="van-glass" x="305" y="1063" width="512" height="175" rx="20"/>
    <rect class="van-glass-light" x="352" y="1078" width="428" height="150" rx="18"/>
    <path class="band-blue" d="M320 1238 L810 1238 L810 1460 Q808 1470 795 1470 L335 1470 Q322 1470 320 1460 Z"/>
    <rect class="van-trim" x="436" y="1288" width="258" height="28" rx="8"/>
    <rect class="van-trim" x="512" y="1327" width="108" height="42" rx="4"/>
    <rect class="lamp-red" x="280" y="1200" width="40" height="195" rx="8"/>
    <rect class="lamp-red" x="810" y="1200" width="42" height="195" rx="8"/>
    <rect class="lamp-clear" x="284" y="1300" width="30" height="50" rx="4"/>
    <rect class="lamp-clear" x="817" y="1300" width="30" height="50" rx="4"/>
    <text class="website" x="565" y="1440" text-anchor="middle">TALLWOODELECTRICALREFRIGERATION.COM.AU</text>
    <text class="email" x="565" y="1459" text-anchor="middle">admin@tallwoodelectricalrefrigeration.com.au</text>
    <path class="van-trim" d="M280 1462 L852 1462 L850 1520 Q848 1530 835 1530 L296 1530 Q284 1530 282 1520 Z"/>
  </g>

  <!-- Front view -->
  <g class="front-view">
    <ellipse class="ground-shadow" cx="1490" cy="1592" rx="320" ry="14"/>
    <rect class="tyre" x="1218" y="1500" width="72" height="90" rx="14"/>
    <rect class="tyre" x="1690" y="1500" width="72" height="90" rx="14"/>
    <path class="van-body" d="M1275 1058 Q1290 1050 1310 1050 L1680 1050 Q1700 1050 1712 1060 L1758 1280 L1760 1330 L1220 1330 L1222 1280 Z"/>
    <path class="van-glass" d="M1285 1065 L1705 1065 Q1718 1068 1722 1080 L1728 1195 Q1728 1203 1718 1203 L1268 1203 Q1258 1203 1258 1195 L1265 1080 Q1270 1066 1285 1065 Z"/>
    <rect class="van-glass-light" x="1300" y="1090" width="390" height="70" rx="10"/>
    <rect class="van-trim" x="1184" y="1165" width="48" height="58" rx="10"/>
    <rect class="van-trim" x="1750" y="1165" width="48" height="58" rx="10"/>
    <path class="lamp-clear" d="M1225 1262 L1305 1275 L1316 1336 L1225 1330 Q1218 1300 1225 1262 Z"/>
    <path class="lamp-clear" d="M1755 1262 L1675 1275 L1664 1336 L1755 1330 Q1762 1300 1755 1262 Z"/>
    <rect class="van-trim" x="1322" y="1322" width="336" height="22" rx="4"/>
    <path class="van-trim" d="M1212 1340 L1306 1340 L1310 1368 L1670 1368 L1674 1340 L1768 1340 L1768 1520 Q1768 1545 1745 1545 L1235 1545 Q1212 1545 1212 1520 Z"/>
    <rect class="van-trim-mid" x="1310" y="1372" width="360" height="42" rx="4"/>
    <rect class="van-trim-mid" x="1325" y="1468" width="330" height="40" rx="4"/>
    <rect class="van-trim-mid" x="1222" y="1385" width="30" height="100" rx="4"/>
    <rect class="van-trim-mid" x="1728" y="1385" width="30" height="100" rx="4"/>
    <line x1="1490" y1="1018" x2="1490" y2="1048" stroke="#2c2d2f" stroke-width="5"/>

    <rect class="brand-square" x="1440" y="1218" width="40" height="40"/>
    <text class="brand-name" x="1486" y="1233" font-size="12">TALLWOOD</text>
    <text class="brand-name" x="1486" y="1246" font-size="8.5">ELECTRICAL &amp;</text>
    <text class="brand-name" x="1486" y="1257" font-size="8.5">REFRIGERATION</text>
  </g>
</svg>
</body>
</html>
```